Super elegant, crisp & clean Business card design required

We recently upgraded our branding - which is on our website - talvendoraphoto.com

I would like a simple, yet elegant, clean business card design please.

The font of my logo is Cinzel - and because of the natural colour - it's best to have this on a black background.

I would like to have the back of the business card - with simply my logo.

PLEASE DO NOT SUBMIT A COMPLICATED / UNCLEAN DESIGN

Industry/Entity Type

Business

Contact Information for Business Card

Talven Doroshko Photography

Font styles to use
Other font styles liked:
• Cinzel

Requirements
Must have
• A backpage with nothing but my logo
• Simple design - stands out
Should not have
• Colour that dont align with my logo
• Over complicated '/ non symmetrical design

```html
<!DOCTYPE html>
<html lang="en">
<head>
<meta charset="utf-8">
<title>Talven Doroshko Photography — Business Card</title>
<link href="https://fonts.googleapis.com/css2?family=Cinzel:wght@400&family=Questrial&display=swap" rel="stylesheet">
<style>
  :root {
    --stage: #1b1b1b;
    --card-black: #000000;
    --card-white: #ffffff;
    --gold: #8e7c62;
    --gold-text: #a38f70;
  }
  * { margin: 0; padding: 0; box-sizing: border-box; }
  html, body { width: 1200px; height: 741px; overflow: hidden; background: var(--stage); }
  .stage { position: relative; width: 1200px; height: 741px; }

  .card { position: absolute; top: 229px; width: 494px; height: 282px; overflow: hidden; }
  .card--back { left: 99px; background: var(--card-black); }
  .card--front { left: 608px; background: var(--card-white); }

  .tab { position: absolute; top: 58px; height: 166px; width: 15px; }
  .tab--left { left: 0; border-radius: 0 9px 9px 0; }
  .tab--right { right: 0; border-radius: 9px 0 0 9px; }
  .card--back .tab { background: var(--gold); }
  .card--front .tab { background: var(--card-black); width: 17px; }

  .wordmark {
    position: absolute; text-align: center; color: var(--gold);
    font-family: "Cinzel", serif; font-weight: 400; line-height: 1;
  }
  .wordmark__name { display: block; letter-spacing: 0.5px; }
  .wordmark__line { display: block; }

  .card--back .wordmark { left: 0; right: 0; top: 168px; }
  .card--back .wordmark__name { font-size: 24px; }
  .card--back .wordmark__line { font-size: 11px; letter-spacing: 10px; margin-top: 3px; padding-left: 10px; }

  .card--front .wordmark { left: 29px; width: 200px; top: 172px; }
  .card--front .wordmark__name { font-size: 16.5px; white-space: nowrap; }
  .card--front .wordmark__line { font-size: 8px; letter-spacing: 7px; margin-top: 2px; padding-left: 7px; }

  .contact-panel {
    position: absolute; left: 243px; top: 58px; width: 251px; height: 166px;
    background: var(--card-black); border-radius: 13px 0 0 13px;
    color: var(--gold-text);
  }
  .person { position: absolute; left: 19px; top: 16px; }
  .person__name { font-family: "Cinzel", serif; font-size: 20px; line-height: 1; letter-spacing: 0.3px; }
  .person__role { font-family: "Questrial", sans-serif; font-size: 13px; margin-top: 1px; }

  .contact-list { position: absolute; left: 19px; top: 97px; list-style: none; font-family: "Questrial", sans-serif; font-size: 12.5px; }
  .contact-list li { display: flex; align-items: center; height: 17.5px; white-space: nowrap; }
  .contact-list svg { width: 11px; height: 11px; margin-right: 7px; flex: none; fill: var(--gold-text); }
  .contact-list .email { font-size: 11px; }
</style>
</head>
<body>
<main class="stage">
  <section class="card card--back" aria-label="Card back">
    <span class="tab tab--left"></span>
    <span class="tab tab--right"></span>
    <div class="wordmark">
      <span class="wordmark__name">Talven Doroshko</span>
      <span class="wordmark__line">PHOTOGRAPHY</span>
    </div>
  </section>

  <section class="card card--front" aria-label="Card front">
    <span class="tab tab--left"></span>
    <div class="wordmark">
      <span class="wordmark__name">Talven Doroshko</span>
      <span class="wordmark__line">PHOTOGRAPHY</span>
    </div>
    <div class="contact-panel">
      <div class="person">
        <p class="person__name">AREN VOSKEL</p>
        <p class="person__role">Chief Executive Officer</p>
      </div>
      <ul class="contact-list">
        <li>
          <svg viewBox="0 0 12 12" aria-hidden="true"><path d="M3 0.5 L5 3 L4 4.3 C4.6 6 5.8 7.4 7.6 8.2 L8.8 7.2 L11.3 9.2 L10 11.3 C5.5 11 1.2 6.5 0.8 2 Z"/></svg>
          <span>44 7700 900415</span>
        </li>
        <li>
          <svg viewBox="0 0 12 12" aria-hidden="true"><path d="M0.5 2.5 H11.5 V9.5 H0.5 Z M1.5 3.3 L6 6.6 L10.5 3.3 V3.2 H1.5 Z"/></svg>
          <span class="email">td.photography@talvendoraphoto.com</span>
        </li>
        <li>
          <svg viewBox="0 0 12 12" aria-hidden="true"><circle cx="6" cy="6" r="5.5" fill="none" stroke="#a38f70" stroke-width="1"/><path d="M0.5 6 H11.5 M6 0.5 V11.5" stroke="#a38f70" stroke-width="0.8"/><ellipse cx="6" cy="6" rx="2.4" ry="5.5" fill="none" stroke="#a38f70" stroke-width="0.8"/></svg>
          <span>www.talvendoraphoto.com</span>
        </li>
      </ul>
    </div>
  </section>
</main>
</body>
</html>
```